Online media outlet needs a blog and logo

A new online blog platform is being established in the UK. The blog will be very similar in layout to www.quorvel.co. It will need to have a main story slider showing three slides and block tiles beneath the slider for additional tiles.

The blog platform will be called 'Tandrel Brisk' and will also need a professional looking logo design for the name.

The website should be designed in Word Press.

Industry/Entity Type

Media

Logo Text

Tandrel Brisk

Coding

Coded - Design and coding required

Number of Pages Required

3 page

Font styles to use
Other font styles liked:
• Helvetica

Requirements
Must have
• A slider showing three slides. Be similar to Quor V (see previous comment). Be Word Press compatible.

```html
<!DOCTYPE html>
<html lang="en">
<head>
<meta charset="utf-8">
<title>Tandrel Brisk</title>
<link rel="stylesheet" href="https://fonts.googleapis.com/css2?family=Roboto:wght@300;400;500;700&family=Oswald:wght@500&display=swap">
<style>
:root{
  --brand:#1380b4;
  --brand-dark:#0c6d9c;
  --ink:#333;
  --muted:#777;
  --nav-active:#3a3a3a;
  --page:#fff;
  --line:#e3e3e3;
  --logo-grey:#9a9a9a;
}
*{box-sizing:border-box;margin:0;padding:0}
html,body{width:1200px;height:3051px;overflow:hidden}
body{font-family:"Roboto",Helvetica,Arial,sans-serif;color:var(--ink);background:var(--page);position:relative}
.wrap{width:1004px;margin:0 auto;position:relative}

/* header */
.topbar{height:95px;background:var(--brand);color:#fff}
.topbar .wrap{display:flex;align-items:center;height:95px;justify-content:space-between}
.brand{font-size:25px;font-weight:500;letter-spacing:.2px}
.top-right{display:flex;align-items:center;gap:14px;font-size:12px}
.top-right .mail{margin-right:10px}
.sq{width:34px;height:34px;background:#fff;border-radius:4px;opacity:.92}

/* hero slider */
.hero{height:585px;position:relative;background:linear-gradient(120deg,#d9dde0 0%,#b9c2c8 35%,#7d8a93 60%,#4b5760 100%)}
.hero-title{position:absolute;top:530px;left:0;right:0;text-align:center;color:#fff;font-size:40px;font-weight:500;letter-spacing:.5px;text-shadow:0 0 3px #000,0 0 2px #000}
.dots{position:absolute;top:637px;left:0;right:0;display:flex;justify-content:center;gap:20px}
.dots span{width:36px;height:5px;background:#c9cdd0}
.dots span.on{background:var(--brand)}

/* nav */
.nav{height:70px;background:var(--brand)}
.nav ul{list-style:none;display:flex;height:70px;align-items:stretch}
.nav li{color:#fff;font-size:12.5px;font-weight:500;display:flex;align-items:center;padding:0 29px}
.nav li.active{background:var(--nav-active);padding:0 26px}

/* tiles */
.row{display:flex;gap:14px}
.tile{position:relative;color:#fff;overflow:hidden}
.tile .photo{position:absolute;inset:0}
.tile .photo::after{content:"";position:absolute;inset:0;background:linear-gradient(180deg,rgba(0,0,0,.15),rgba(0,0,0,0) 35%,rgba(0,0,0,.55))}
.kicker{position:absolute;top:14px;left:16px;font-size:11.5px;font-weight:500;z-index:1}
.tile .title{position:absolute;left:16px;right:16px;bottom:42px;font-size:15px;font-weight:700;line-height:1.35;z-index:1}
.meta{position:absolute;left:16px;right:16px;bottom:14px;display:flex;justify-content:space-between;align-items:center;font-size:11.5px;z-index:1}
.icons{display:flex;gap:7px}
.icons i{display:block;width:8px;height:8px;background:currentColor;border-radius:2px}
.small-tile{width:325px;height:227px}

/* text card */
.card{width:325px;border:1px solid var(--line);background:#fff;position:relative}
.card .photo{height:240px}
.card .body{padding:14px 18px}
.card .kicker2{color:var(--brand);font-size:11.5px;margin-bottom:10px}
.card h3{font-size:15.5px;font-weight:400;line-height:1.35;margin-bottom:14px;color:#333}
.card p{font-size:11.3px;line-height:1.65;color:var(--muted);margin-bottom:12px}
.card .meta{position:static;color:var(--brand)}

/* newsletter band */
.briefing{height:265px;margin-top:50px;background:linear-gradient(90deg,#3b4650,#5b6670 45%,#4a5560);color:#fff;text-align:center;padding-top:38px}
.briefing h2{font-size:25px;font-weight:400;margin-bottom:12px}
.briefing p{font-size:12.5px;line-height:1.7;opacity:.95}
.brief-form{display:flex;justify-content:center;gap:25px;margin-top:30px}
.field{height:48px;background:#fff;color:#888;font-size:12.5px;display:flex;align-items:center;padding-left:16px;text-align:left}
.f-mail{width:295px}.f-freq{width:270px}
.btn-sub{width:151px;height:48px;border:1px solid #fff;display:flex;align-items:center;justify-content:center;font-size:13.5px;font-weight:500}

/* partners */
.partners{display:flex;justify-content:space-between;align-items:center;height:120px;color:var(--logo-grey);font-size:27px;font-weight:500;padding:0 20px}

/* footer */
.footer{position:absolute;left:0;right:0;top:2787px;height:264px;background:var(--brand);color:#fff}
.cols{display:flex;padding-top:38px}
.col h4{font-size:14.5px;font-weight:500;margin-bottom:18px}
.col{font-size:11px;line-height:1.75}
.c1{width:268px}.c2{width:300px}.c3{width:300px}
.contact-line{display:flex;align-items:center;gap:12px;margin-top:8px}
.contact-line.phone{font-size:17px;margin-top:14px}
.tweet{display:flex;gap:14px}
.tweet .sq{width:18px;height:18px;flex:none;border-radius:3px}
.news-form{display:flex;margin-top:24px}
.news-form .in{width:170px;height:40px;background:#fff;color:#444;font-size:10.5px;display:flex;align-items:center;padding-left:10px}
.news-form .go{width:70px;height:40px;background:#2d3a44;display:flex;align-items:center;justify-content:center;font-size:15px}
.soc{display:flex;gap:16px}
.copyright{position:absolute;bottom:18px;left:0;right:0;text-align:center;font-size:12px}
</style>
</head>
<body>

<header class="topbar">
  <div class="wrap">
    <div class="brand">Tandrel Brisk</div>
    <div class="top-right">
      <span class="mail">info@tandrelbrisk.com</span>
      <span class="sq"></span><span class="sq"></span><span class="sq"></span>
    </div>
  </div>
</header>

<section class="hero" role="img" aria-label="Slide photo: coffee mug and glasses beside a person typing on a laptop">
  <h1 class="hero-title">ACCUSANTIUM DOLOREMQUE</h1>
  <div class="dots"><span></span><span class="on"></span></div>
</section>

<nav class="nav">
  <ul class="wrap">
    <li class="active">HOME</li><li>CURRENT TOPICS</li><li>WEEKEND</li><li>GOVERNMENT</li><li>POLITICS</li><li>COMPETITION</li><li>INVESTMENT</li><li>CONTACT</li>
  </ul>
</nav>

<main>
  <div class="wrap row" style="margin-top:47px">
    <article class="tile small-tile">
      <div class="photo" role="img" aria-label="Photo of hands working on a laptop" style="background:linear-gradient(135deg,#2f3a44,#5d6b76)"></div>
      <span class="kicker">Dummy text</span>
      <h3 class="title">There are many variations of passages of Lorem Ipsum available.</h3>
      <div class="meta"><span>3 May 2016</span><span class="icons"><i></i><i></i><i></i><i></i></span></div>
    </article>
    <article class="tile small-tile">
      <div class="photo" role="img" aria-label="Photo of a woman in a bright living room" style="background:linear-gradient(135deg,#c8b8a4,#8f7c6a)"></div>
      <span class="kicker">Dummy text</span>
      <h3 class="title">Predefined chunks necessary, making this the first true generator.net.</h3>
      <div class="meta"><span>3 May 2016</span><span class="icons"><i></i><i></i><i></i><i></i></span></div>
    </article>
    <article class="tile small-tile">
      <div class="photo" role="img" aria-label="Photo of a digital world map with business words" style="background:linear-gradient(135deg,#9fb8c8,#49657a)"></div>
      <span class="kicker">Dummy text</span>
      <h3 class="title">Many desktop publishing packages and web page editors now use</h3>
      <div class="meta"><span>3 May 2016</span><span class="icons"><i></i><i></i><i></i><i></i></span></div>
    </article>
  </div>

  <div class="wrap row" style="margin-top:47px">
    <article class="card" style="height:483px">
      <div class="photo" role="img" aria-label="Photo of a framed social media sign on a desk" style="background:linear-gradient(135deg,#3b3b3b,#6e6e6e)"></div>
      <div class="body">
        <div class="kicker2">Dummy text</div>
        <h3>There are many variations of passages of Lorem Ipsum available.</h3>
        <p>There are many variations of passages of Lorem Ipsum available, but the majority have suffered alteration in some form, by injected humour, or randomised words which don't look even slightly believable. If you are going to use a passage of Lorem Ipsum, you need to be sure there isn't anything</p>
        <div class="meta"><span>4 May 2016</span><span class="icons"><i></i><i></i><i></i><i></i></span></div>
      </div>
    </article>
    <article class="tile" style="width:665px;height:483px">
      <div class="photo" role="img" aria-label="Photo of a businessman using a phone beside a laptop and coffee" style="background:linear-gradient(135deg,#c9cdd0,#8b8f93 45%,#3d4146)"></div>
      <span class="kicker">Dummy text</span>
      <h3 class="title">There are many variations of passages of Lorem Ipsum available, but the majority have suffered alteration in some form, by injected humour.</h3>
      <div class="meta"><span>3 May 2016</span><span class="icons"><i></i><i></i><i></i><i></i></span></div>
    </article>
  </div>

  <section class="briefing" role="img" aria-label="Background photo of app icons on a tablet screen">
    <h2>Tandrel Brisk Email Briefings</h2>
    <p>Denouncing pleasure and praising pain was born and I will give you a complete account of the system,<br>and expound the actual teachings of the great explorer of the truth, the master-builder.</p>
    <div class="brief-form">
      <div class="field f-mail">Your e-mail</div>
      <div class="field f-freq">Daily</div>
      <div class="btn-sub">SUBSCRIBE</div>
    </div>
  </section>

  <div class="wrap row" style="margin-top:45px">
    <article class="tile" style="width:665px;height:482px">
      <div class="photo" role="img" aria-label="Illustration of people around a table with social media doodles" style="background:linear-gradient(135deg,#a9abad,#7f8285)"></div>
      <span class="kicker">Dummy text</span>
      <h3 class="title">There are many variations of passages of Lorem Ipsum available, but the majority have suffered alteration in some form, by injected humour.</h3>
      <div class="meta"><span>3 May 2016</span><span class="icons"><i></i><i></i><i></i><i></i></span></div>
    </article>
    <article class="card" style="height:482px">
      <div class="photo" role="img" aria-label="Photo of hands holding a card over a laptop keyboard" style="background:linear-gradient(135deg,#c7c2c6,#8c8790)"></div>
      <div class="body">
        <div class="kicker2">Dummy text</div>
        <h3>There are many variations of passages of Lorem Ipsum available.</h3>
        <p>There are many variations of passages of Lorem Ipsum available, but the majority have suffered alteration in some form, by injected humour, or randomised words which don't look even slightly believable. If you are going to use a passage of Lorem Ipsum, you need to be sure there isn't anything</p>
        <div class="meta"><span>4 May 2016</span><span class="icons"><i></i><i></i><i></i><i></i></span></div>
      </div>
    </article>
  </div>

  <div class="wrap row" style="margin-top:46px">
    <article class="tile small-tile">
      <div class="photo" role="img" aria-label="Photo of a hand touching glowing network icons" style="background:linear-gradient(135deg,#16324a,#3f6a8c)"></div>
      <span class="kicker">Dummy text</span>
      <h3 class="title">There are many variations of passages of Lorem Ipsum available.</h3>
      <div class="meta"><span>3 May 2016</span><span class="icons"><i></i><i></i><i></i><i></i></span></div>
    </article>
    <article class="tile small-tile">
      <div class="photo" role="img" aria-label="Photo of a person with a laptop and orange icon overlay" style="background:linear-gradient(135deg,#c4582a,#7a3a22)"></div>
      <span class="kicker">Dummy text</span>
      <h3 class="title">Predefined chunks necessary, making this the first true generator.net.</h3>
      <div class="meta"><span>3 May 2016</span><span class="icons"><i></i><i></i><i></i><i></i></span></div>
    </article>
    <article class="tile small-tile">
      <div class="photo" role="img" aria-label="Photo of a laptop with glowing connected icons" style="background:linear-gradient(135deg,#5c6e7a,#b08a4a)"></div>
      <span class="kicker">Dummy text</span>
      <h3 class="title">Many desktop publishing packages and web page editors now use</h3>
      <div class="meta"><span>3 May 2016</span><span class="icons"><i></i><i></i><i></i><i></i></span></div>
    </article>
  </div>

  <div class="wrap partners">
    <span>KARVO</span><span>Lumeno</span><span>BRANTIS</span><span>Ostery</span><span>verdal</span><span>FENNIX</span>
  </div>
</main>

<footer class="footer">
  <div class="wrap cols">
    <div class="col c1">
      <h4>CONTACT US</h4>
      <div>27 Veldt Row 5th Floor<br>Marlow, NY 10018, UK</div>
      <div class="contact-line phone">
        <svg width="16" height="16" viewBox="0 0 16 16"><path d="M3 1l3 3-2 2c1 2 3 4 5 5l2-2 3 3-2 3C7 14 2 9 1 3z" fill="none" stroke="#fff" stroke-width="1.3"/></svg>
        (+901) 555-0142
      </div>
      <div class="contact-line">
        <svg width="16" height="12" viewBox="0 0 16 12"><rect x=".7" y=".7" width="14.6" height="10.6" fill="none" stroke="#fff" stroke-width="1.3"/><path d="M1 1l7 6 7-6" fill="none" stroke="#fff" stroke-width="1.3"/></svg>
        info@tandrelbrisk.com
      </div>
    </div>
    <div class="col c2">
      <h4>LATEST TWEET`S</h4>
      <div class="tweet"><span class="sq"></span>
        <div>Phasellus porta. Fusce suscit varius<br>mi. Cum sociis natoque penatibus et<br>magnis dis parturient montes, nasce-<br>tur ridiculus mus. See more here<br>http://t.co/Qx7Rm20kT</div>
      </div>
    </div>
    <div class="col c3">
      <h4>NEWSLETTER</h4>
      <div>Excepteur sint occaecat cupidatat non proident,<br>sunt in culpa qui officia deserunt mollit anim</div>
      <div class="news-form"><div class="in">Enter your email address</div><div class="go">Sign Up</div></div>
    </div>
    <div class="col">
      <h4>SOCIAL MEDIA</h4>
      <div class="soc"><span class="sq"></span><span class="sq"></span><span class="sq"></span></div>
    </div>
  </div>
  <div class="copyright">2016 &nbsp;All Rights Reserved.</div>
</footer>

</body>
</html>
```